MirelaStyle e-commerce website design for shopify platform

I currently have a trendy e-commerce clothing store that is primarily based off of the Southern California Style/Trends. I am looking for a redesign of my shopify template as I don't like my current image. I am looking for a sleek clean design that allows more focus on the products. I like neutral backgrounds and easy to use websites. Should be responsive to mobile devices. I would also like to have some ideas for a slide show picture that notifies customers of free shipping if possible. I do also have a theme template that I purchased through Shopify so one could set the theme up for me and edit it to what I need. My website is mirelastyle.com if you would like to look at the type of products I have. I am also looking to do a logo redesign as well- looking for a more stylish logo that would appeal to an approximate age range of 18-40 year old women. I want to be remembered, something to match the web design.

I like teal/turquoise and grey combos but I don't have to have this as the colors.

Target Market(s)

approx. 18-40

Industry/Entity Type

E-Commerce

Number of Pages Required

2 page

Requirements
Must have
• Menu bar, shopify compatible, easy to access/navigate, responsive to mobile devices, easy product upload
Nice to have
• if able ability to resize pictures all to the same size
Should not have
• not be difficult to navigate both on a reg. computer or mobile device

```html
<!DOCTYPE html>
<html lang="en">
<head>
<meta charset="utf-8">
<title>MirelaStyle – Best Online Store</title>
<link rel="stylesheet" href="https://fonts.googleapis.com/css2?family=Open+Sans:wght@300;400;600&family=Oswald:wght@400&display=swap">
<style>
:root{
  --teal:#13898e;
  --teal-dark:#0d6d71;
  --ink:#333;
  --muted:#666;
  --band:#efefef;
  --footer:#f1f1f1;
  --line:#dcdcdc;
  --white:#fff;
}
*{margin:0;padding:0;box-sizing:border-box}
html,body{width:1200px;height:2980px;overflow:hidden}
body{position:relative;background:var(--white);font-family:"Open Sans",Arial,sans-serif;color:var(--ink)}
.abs{position:absolute}
a{color:inherit;text-decoration:none}

/* top bar */
.topbar{left:0;top:0;width:1200px;height:40px;background:var(--teal);color:var(--white);font-size:12px}
.toplinks{left:100px;top:0;height:40px;display:flex;align-items:center;gap:22px}
.toplinks span{display:flex;align-items:center;gap:6px}
.search{left:834px;top:6px;width:240px;height:26px;background:#e9e9e9;font-size:12px;color:#888;padding:5px 10px}
.search-btn{left:1074px;top:6px;width:26px;height:26px;background:#1d4f52;display:flex;align-items:center;justify-content:center}

/* header */
.logo{left:78px;top:86px;display:flex;align-items:center;gap:10px;font-size:38px;font-weight:600;color:#222}
.logo i{width:16px;height:16px;border-radius:50%;background:var(--teal);display:block}
.nav{left:368px;top:93px;height:40px;display:flex;align-items:center;font-size:13px;color:#444}
.nav a{margin-right:26px}
.nav .current{background:var(--teal);color:var(--white);padding:0 14px;height:40px;line-height:40px;font-weight:600;margin-right:30px}
.cart-btn{left:1040px;top:85px;width:60px;height:56px;background:var(--teal);display:flex;align-items:center;justify-content:center}

/* hero */
.hero{left:0;top:183px;width:1200px;height:493px;background:linear-gradient(100deg,#e9e4dc 0%,#f3eee6 35%,#f6efe5 55%,#d7cfc4 100%)}
.hero-figure{left:600px;top:183px;width:260px;height:493px;background:linear-gradient(180deg,#d8c2b0 0%,#eef0f4 45%,#cfd6e6 70%,#e9ddd0 100%);opacity:.75}
.hero-kicker{left:125px;top:346px;font-size:22px;color:var(--teal)}
.hero-title{left:123px;top:375px;font-size:46px;color:#222}
.hero-cta{left:131px;top:457px;width:170px;height:48px;border-radius:24px;background:var(--teal);color:var(--white);font-size:16px;display:flex;align-items:center;justify-content:center}
.hero-arrow{top:390px;width:62px;height:62px;border-radius:50%;display:flex;align-items:center;justify-content:center}
.hero-arrow.prev{left:39px;background:rgba(160,150,140,.55)}
.hero-arrow.next{left:1099px;background:rgba(120,190,180,.7)}
.offer-badge{left:954px;top:183px;width:58px;height:82px;background:var(--teal);border-radius:0 0 29px 29px;color:var(--white);font-size:12px;text-align:center;padding-top:10px;line-height:32px}
.offer-badge b{display:block;font-weight:600;background:#1d4f52;line-height:22px;margin:0 4px}
.slider-track{left:100px;top:672px;width:308px;height:4px;background:var(--teal)}

/* about */
.about-title{left:0;top:722px;width:1200px;text-align:center;font-size:23px;color:#222}
.about-text{left:110px;top:775px;width:980px;text-align:center;font-size:12.5px;line-height:20px;color:#444}
.about-btn{left:543px;top:832px;width:110px;height:29px;background:var(--teal);color:var(--white);font-size:12px;display:flex;align-items:center;justify-content:center}

/* section bars */
.band{left:0;width:1200px;height:46px;background:var(--band)}
.band-label{left:100px;height:46px;background:var(--teal);color:var(--white);font-family:"Oswald",Arial,sans-serif;font-size:19px;padding:0 26px;display:flex;align-items:center}
.band-ctrl{width:32px;height:46px;display:flex;align-items:center;justify-content:center}

/* products */
.product{width:236px}
.product .photo{width:236px;height:358px}
.product .name{margin-top:12px;text-align:center;font-size:15px;font-family:Arial,sans-serif;color:#444}
.price-tag{left:264px;top:1010px;width:70px;height:70px;overflow:hidden}
.price-tag div{position:absolute;left:-8px;top:22px;width:120px;height:28px;background:var(--teal);color:var(--white);font-size:13px;font-weight:600;text-align:center;line-height:28px;transform:rotate(45deg)}
.quick-actions{left:100px;top:1303px;width:236px;height:67px;display:flex}
.quick-actions div{flex:1;display:flex;align-items:center;justify-content:center;background:rgba(110,110,110,.75)}
.quick-actions div:first-child{background:var(--teal)}

/* promos */
.promo-collection{left:100px;top:2007px;width:278px;height:354px;background:linear-gradient(160deg,#f4f1ee 0%,#d9d2cc 45%,#2b2a2c 100%)}
.collection-tag{left:155px;width:173px;height:38px;background:rgba(40,40,40,.75);color:var(--white);font-size:24px;display:flex;align-items:center;justify-content:center}
.promo-tops{left:411px;top:2007px;width:688px;height:159px;background:#fde8de}
.promo-tops-photo{left:457px;top:2007px;width:199px;height:159px;background:linear-gradient(180deg,#f3e3d4,#cfd9ea)}
.promo-beach{left:411px;top:2202px;width:688px;height:159px;background:linear-gradient(180deg,#cfe9ea 0%,#e8f2f1 45%,#e7ebe9 100%)}
.coupon{background:var(--white);padding:4px 10px;margin-left:8px}

/* footer */
.like-band{left:0;top:2464px;width:1200px;height:64px;background:#f6f6f6}
.like-title{left:100px;top:2472px;font-size:30px;font-weight:300;color:#444}
.social{top:2476px;width:42px;height:42px;border-radius:50%;background:var(--white);border:3px solid}
.footer{left:0;top:2528px;width:1200px;height:393px;background:var(--footer)}
.fcol{top:2552px;width:230px;font-size:12px;line-height:18px;color:#555}
.fcol h3{font-family:"Oswald",Arial,sans-serif;font-weight:400;font-size:17px;color:var(--teal);margin-bottom:24px}
.frow{display:flex;gap:16px;margin-bottom:22px}
.frow svg{flex:none;margin-top:2px}
.subscribe{width:212px;height:30px;border:1px solid var(--line);background:var(--white);font-size:11px;color:#777;padding:6px 10px;margin:24px 0 10px}
.signup{width:212px;height:28px;background:var(--teal);color:var(--white);font-size:11px;font-weight:600;text-align:center;line-height:28px}
.fb-box{width:236px;height:260px;background:var(--white);border:1px solid #e3e3e3;padding:14px 10px;font-size:10px}
.fb-head{display:flex;gap:8px;align-items:flex-start}
.fb-sq{width:50px;height:50px;background:#3b5a95}
.fb-faces{display:grid;grid-template-columns:repeat(5,40px);gap:8px;margin-top:8px}
.fb-faces div{width:40px;height:40px;background:#b9b1ab}
.bottombar{left:0;top:2921px;width:1200px;height:59px;background:var(--teal);color:var(--white);font-size:12px}
.copyright{left:100px;top:0;height:59px;display:flex;align-items:center;gap:14px}
.cards{left:910px;top:17px;display:flex;gap:12px}
.cards div{width:40px;height:26px;border-radius:3px;background:var(--white)}
</style>
</head>
<body>

<!-- Top bar -->
<div class="abs topbar">
  <div class="abs toplinks">
    <span><svg width="11" height="10" viewBox="0 0 11 10"><path d="M5.5 9.5 1 5a2.5 2.5 0 0 1 4.5-3.3A2.5 2.5 0 0 1 10 5z" fill="#fff"/></svg>Wish List (0)</span>
    <span><svg width="10" height="11" viewBox="0 0 10 11"><circle cx="5" cy="3" r="2.6" fill="#fff"/><path d="M0 11a5 5 0 0 1 10 0z" fill="#fff"/></svg>My Account</span>
    <span><svg width="13" height="11" viewBox="0 0 13 11"><path d="M0 1h2.5l2 6h6.5l1.5-4.5H4" fill="none" stroke="#fff" stroke-width="1.5"/><circle cx="5" cy="9.5" r="1.2" fill="#fff"/><circle cx="10" cy="9.5" r="1.2" fill="#fff"/></svg>Shopping Cart</span>
    <span><svg width="11" height="10" viewBox="0 0 11 10"><path d="M1 5l3 3 6-7" fill="none" stroke="#fff" stroke-width="2"/></svg>Checkout</span>
  </div>
</div>
<div class="abs search">Search</div>
<div class="abs search-btn"><svg width="13" height="13" viewBox="0 0 13 13"><circle cx="5.5" cy="5.5" r="4" fill="none" stroke="#fff" stroke-width="1.8"/><path d="M8.5 8.5 12 12" stroke="#fff" stroke-width="2"/></svg></div>

<!-- Header -->
<div class="abs logo"><i></i>MirelaStyle</div>
<nav class="abs nav">
  <a class="current">What's New?</a>
  <a>Dresses</a><a>Tops</a><a>Bottoms/Rompers</a><a>Accessories</a><a>Sale</a><a>A little about me...</a>
</nav>
<div class="abs cart-btn"><svg width="22" height="26" viewBox="0 0 22 26"><path d="M7 8V5a4 4 0 0 1 8 0v3" fill="none" stroke="#fff" stroke-width="2"/><rect x="1" y="8" width="20" height="17" rx="2" fill="#fff"/></svg></div>

<!-- Hero -->
<div class="abs hero" role="img" aria-label="Sunlit beach scene with a model in a floral strapless summer dress"></div>
<div class="abs hero-figure"></div>
<div class="abs hero-kicker">MirelaStyle</div>
<div class="abs hero-title">Best Online Store</div>
<a class="abs hero-cta">Join Us</a>
<div class="abs hero-arrow prev"><svg width="14" height="18" viewBox="0 0 14 18"><path d="M12 1 2 9l10 8z" fill="#fff"/></svg></div>
<div class="abs hero-arrow next"><svg width="14" height="18" viewBox="0 0 14 18"><path d="M2 1l10 8-10 8z" fill="#fff"/></svg></div>
<div class="abs offer-badge"><b>NEW</b>Offer's</div>
<div class="abs slider-track"></div>

<!-- About -->
<h2 class="abs about-title" style="font-weight:400">A LITTLE ABOUT ME...</h2>
<p class="abs about-text">My name is Mirela (pronounced Meerla with a "J") and I have always loved fashion! In 2004, I moved to LA to pursue my love. I have finally made it a reality by opening my own boutique. We currently carry a variety of different labels and hope to incorporate our own in the near future!</p>
<a class="abs about-btn">Read More</a>

<!-- New Product -->
<div class="abs band" style="top:924px"></div>
<div class="abs band-label" style="top:924px">New Product</div>
<div class="abs band-ctrl" style="left:1036px;top:924px;background:#c9c9c9"><svg width="8" height="10"><path d="M7 0 0 5l7 5z" fill="#fff"/></svg></div>
<div class="abs band-ctrl" style="left:1068px;top:924px;background:var(--teal)"><svg width="8" height="10"><path d="M1 0l7 5-7 5z" fill="#fff"/></svg></div>

<div class="abs product" style="left:100px;top:1010px"><div class="photo" role="img" aria-label="Model in a white off-shoulder top" style="background:linear-gradient(180deg,#d9d9db,#c3c3c6)"></div><p class="name">Lorem ipsum</p></div>
<div class="abs product" style="left:354px;top:1010px"><div class="photo" role="img" aria-label="Model in a white tunic with black embroidered neckline" style="background:linear-gradient(180deg,#d2d4d8,#e7e7e9)"></div><p class="name">Lorem ipsum</p></div>
<div class="abs product" style="left:610px;top:1010px"><div class="photo" role="img" aria-label="Model in a white tee and daisy print shorts" style="background:linear-gradient(180deg,#e2e2e3,#3a3a38)"></div><p class="name">Lorem ipsum</p></div>
<div class="abs product" style="left:864px;top:1010px"><div class="photo" role="img" aria-label="Blue patterned flare pants" style="background:linear-gradient(90deg,#a8b4c0,#2a4f77,#a8b4c0)"></div><p class="name">Lorem ipsum</p></div>

<div class="abs price-tag"><div>$ 292.39</div></div>
<div class="abs quick-actions">
  <div><svg width="20" height="24" viewBox="0 0 22 26"><path d="M7 8V5a4 4 0 0 1 8 0v3" fill="none" stroke="#fff" stroke-width="2"/><rect x="1" y="8" width="20" height="17" rx="2" fill="#fff"/></svg></div>
  <div><svg width="22" height="22" viewBox="0 0 22 22"><rect x="2" y="8" width="11" height="6" rx="3" transform="rotate(-45 7.5 11)" fill="none" stroke="#fff" stroke-width="2"/><rect x="9" y="8" width="11" height="6" rx="3" transform="rotate(-45 14.5 11)" fill="none" stroke="#fff" stroke-width="2"/></svg></div>
  <div><svg width="22" height="22" viewBox="0 0 22 22"><path d="M4 9a7 7 0 0 1 13-2M18 13a7 7 0 0 1-13 2" fill="none" stroke="#fff" stroke-width="2.4"/><path d="M18 2v6h-6M4 20v-6h6" fill="none" stroke="#fff" stroke-width="2.4"/></svg></div>
</div>

<!-- Seasonal -->
<div class="abs band" style="top:1474px"></div>
<div class="abs band-label" style="top:1474px">Seasonal Must Haves</div>
<div class="abs band-ctrl" style="left:1036px;top:1474px;background:#c9c9c9"><svg width="8" height="10"><path d="M7 0 0 5l7 5z" fill="#fff"/></svg></div>
<div class="abs band-ctrl" style="left:1068px;top:1474px;background:var(--teal)"><svg width="8" height="10"><path d="M1 0l7 5-7 5z" fill="#fff"/></svg></div>

<div class="abs product" style="left:100px;top:1562px"><div class="photo" role="img" aria-label="White lace flare pants" style="background:linear-gradient(180deg,#f0ebe3,#e4dccf)"></div><p class="name">Lorem ipsum</p></div>
<div class="abs product" style="left:354px;top:1562px"><div class="photo" role="img" aria-label="Cream crochet drawstring pants" style="background:linear-gradient(180deg,#f4efe6,#e6dcc9)"></div><p class="name">Lorem ipsum</p></div>
<div class="abs product" style="left:610px;top:1562px"><div class="photo" role="img" aria-label="Red floral print flare pants" style="background:linear-gradient(90deg,#e9e9e9,#8a3a3c,#e9e9e9)"></div><p class="name">Lorem ipsum</p></div>
<div class="abs product" style="left:864px;top:1562px"><div class="photo" role="img" aria-label="Tribal print flare pants" style="background:linear-gradient(90deg,#a4a8b0,#6a3a2c,#a4a8b0)"></div><p class="name">Lorem ipsum</p></div>

<!-- Promos -->
<div class="abs promo-collection" role="img" aria-label="Model in a black lace top for the summer collection"></div>
<div class="abs collection-tag" style="top:2100px">New</div>
<div class="abs collection-tag" style="top:2170px;color:#5fc2c0">Summer</div>
<div class="abs collection-tag" style="top:2240px">Collections</div>

<div class="abs promo-tops"></div>
<div class="abs promo-tops-photo" role="img" aria-label="Woman in a light blue shirt with glasses"></div>
<div class="abs" style="left:861px;top:2032px;font-size:16px;color:#333">Women Tops</div>
<div class="abs" style="left:836px;top:2066px;font-size:27px;color:#333"><span style="color:#e2674a;font-style:italic">30%</span> Flat offer</div>
<div class="abs" style="left:776px;top:2116px;font-size:15px;color:#333">Use this cuppon code:<span class="coupon">M362K2KL</span></div>

<div class="abs promo-beach" role="img" aria-label="Woman in a white dress and heels lying on the beach"></div>
<div class="abs" style="left:711px;top:2232px;width:100px;text-align:center;font-size:16px">Lorem ipsum</div>
<div class="abs" style="left:661px;top:2260px;width:200px;text-align:center;font-size:27px"><i>10%</i> discount</div>
<div class="abs" style="left:661px;top:2302px;width:200px;text-align:center;font-size:16px">on every product</div>

<!-- Like band -->
<div class="abs like-band"></div>
<div class="abs like-title">Like Us to Spread the World</div>
<div class="abs social" style="left:842px;border-color:#9fb8dd"></div>
<div class="abs social" style="left:896px;border-color:#e6a6a6"></div>
<div class="abs social" style="left:950px;border-color:#9fcde6"></div>
<div class="abs social" style="left:1004px;border-color:#f0c98e"></div>
<div class="abs social" style="left:1058px;border-color:#c4b2dc"></div>

<!-- Footer -->
<div class="abs footer"></div>
<div class="abs fcol" style="left:100px">
  <h3>Sample column</h3>
  <p>This is a CMS block edited from admin panel. You can insert any content here.</p><br>
  <p>Lorem ipsum dolor sit amet, consectetur adipiscing elit. Pellentesque non dui at sapien tempor gravida ut vel arcu. Maecenas odio arcu, feugiat vel congue feugiat, laoreet vitae diam.</p>
  <div class="subscribe">Enter Your email Is</div>
  <div class="signup">SIGNUP</div>
</div>
<div class="abs fcol" style="left:348px">
  <h3>Contact us</h3>
  <div class="frow"><svg width="12" height="16" viewBox="0 0 12 16"><path d="M6 16S0 9 0 6a6 6 0 0 1 12 0c0 3-6 10-6 10z" fill="var(--teal)"/><circle cx="6" cy="6" r="2.2" fill="#fff"/></svg><p>Mirela Boutique<br>18 Harbor Lane 2210, Coral Tower<br>Seaside Rd, 9021SC</p></div>
  <div class="frow"><svg width="12" height="14" viewBox="0 0 12 14"><rect x="1" y="1" width="10" height="12" rx="1.5" fill="none" stroke="#999" stroke-width="1.4"/></svg><p>+1 800 555 0142</p></div>
  <div class="frow"><svg width="14" height="11" viewBox="0 0 14 11"><rect x="1" y="1" width="12" height="9" fill="none" stroke="#999" stroke-width="1.3"/><path d="M1 1l6 5 6-5" fill="none" stroke="#999" stroke-width="1.3"/></svg><p>hello@mirelastyle.com</p></div>
  <div class="frow"><svg width="13" height="13" viewBox="0 0 13 13"><circle cx="6.5" cy="6.5" r="5.5" fill="none" stroke="#999" stroke-width="1.4"/></svg><p>mirelashop</p></div>
</div>
<div class="abs fcol" style="left:600px">
  <h3>Chirpline</h3>
  <div class="frow"><svg width="13" height="11" viewBox="0 0 13 11"><circle cx="6.5" cy="5.5" r="4.5" fill="var(--teal)"/></svg><p>Lorem ipsum dolor sit amet, consectetur adipiscing elit. Pellentesque non dui at sapien tempor gravida ut vel arcu.<br>9 days ago</p></div>
  <div class="frow"><svg width="13" height="11" viewBox="0 0 13 11"><circle cx="6.5" cy="5.5" r="4.5" fill="var(--teal)"/></svg><p>Donec porta enim sit amet augue iaculis eu volutpat ligula pharetra. Ut nec dui nec nisi consectetur sodales.<br>3 days ago</p></div>
  <p style="font-size:11px;margin-left:29px"><span style="color:var(--teal)">Follow us</span> on Chirpline</p>
</div>
<div class="abs fcol" style="left:850px">
  <h3>Friendbook</h3>
  <div class="fb-box">
    <div class="fb-head"><div class="fb-sq"></div><div><b style="color:#3b5a95;font-size:12px">MirelaStyle</b><br><span style="border:1px solid #ccc;padding:0 5px">Like</span></div></div>
    <p style="margin-top:8px">12,480 people like MirelaStyle.</p>
    <div class="fb-faces"><div></div><div></div><div></div><div></div><div></div><div></div><div></div><div></div><div></div><div></div><div></div><div></div></div>
  </div>
</div>

<!-- Bottom bar -->
<div class="abs bottombar">
  <div class="abs copyright"><span>Copyright © mirelastyle.com</span>|<span>Privacy</span>|<span>Sitemap</span>|<span>T&amp;C</span></div>
  <div class="abs cards"><div></div><div></div><div></div><div></div></div>
</div>

</body>
</html>
```